Brisk Harbor claims recovery services

Its a new company in Dubai UAE. The company activity is debt management, debt collection, loans settlements and restructuring. The company involved in any business or sector requires debt management including government entities, Medical & Health care sector, Banks & finance companies, SME's and commercial business.

Target Market(s)

government entities, Medical & Health care sector, Banks & finance companies, SME's and commercial business.

Industry/Entity Type

Financial Service

Number of Pages Required

5+ page

Requirements
Must have
• Focus on the services not the team and clients
Should not have
• Colorful . Shouldn't have Client testimonial and our clients

```html
<!DOCTYPE html>
<html lang="en">
<head>
<meta charset="utf-8">
<title>Brisk Harbor – Claims Recovery Services</title>
<link rel="stylesheet" href="https://fonts.googleapis.com/css2?family=Cinzel:wght@400;700&family=Lato:wght@700;900&family=Open+Sans:wght@400;700&family=Roboto+Condensed:wght@400;700&display=swap">
<style>
  :root {
    --brand-blue: #2a5f8c;
    --deep-blue: #0d4a73;
    --band-blue: #0a4e78;
    --grey-title: #8a8a8a;
    --text-grey: #666666;
    --nav-grey: #8c8c8c;
    --footer-bg: #333333;
    --footer-line: #555555;
    --footer-text: #5e5e5e;
    --white: #ffffff;
    --icon-fill: #5b87a6;
  }
  * { margin: 0; padding: 0; box-sizing: border-box; }
  html, body { width: 1200px; height: 2222px; overflow: hidden; background: var(--white); }
  .page { position: relative; width: 1200px; height: 2222px; overflow: hidden; font-family: "Open Sans", Arial, sans-serif; }

  /* Header */
  .site-header { position: absolute; top: 0; left: 0; width: 1200px; height: 124px; background: var(--white); }
  .brand { position: absolute; left: 77px; top: 22px; display: flex; align-items: center; gap: 16px; }
  .brand-mark { width: 70px; height: 70px; border-radius: 50%; background: var(--brand-blue); }
  .brand-name { font-family: "Cinzel", Georgia, serif; font-size: 36px; font-weight: 400; color: var(--brand-blue); line-height: 1; letter-spacing: 1px; }
  .brand-tagline { font-family: "Cinzel", Georgia, serif; font-size: 9px; letter-spacing: 5px; color: var(--nav-grey); margin-top: 6px; }
  .main-nav { position: absolute; top: 47px; left: 487px; display: flex; gap: 0; }
  .main-nav a { font-family: "Cinzel", Georgia, serif; font-size: 19px; color: var(--nav-grey); text-decoration: none; letter-spacing: .5px; margin-right: 46px; }
  .main-nav a:last-child { margin-right: 0; }
  .main-nav a.active { color: var(--brand-blue); }

  /* Hero */
  .hero { position: absolute; top: 124px; left: 0; width: 1200px; height: 574px; }
  .hero-photo { position: absolute; inset: 0; background: linear-gradient(100deg, #3e3530 0%, #5a4d45 45%, #8e8a88 62%, #dcdcde 80%, #bfbcbc 100%); }
  .hero-title { position: absolute; left: 79px; top: 146px; font-family: "Lato", Arial, sans-serif; font-weight: 900; font-size: 41px; line-height: 63px; color: var(--white); text-transform: uppercase; }
  .hero-button { position: absolute; left: 77px; top: 352px; width: 197px; height: 61px; border: 2px solid var(--white); border-radius: 3px; color: var(--white); font-family: "Roboto Condensed", Arial, sans-serif; font-weight: 700; font-size: 23px; display: flex; align-items: center; justify-content: center; }
  .slider-dots { position: absolute; left: 528px; top: 505px; display: flex; gap: 13px; }
  .slider-dots span { width: 18px; height: 18px; border-radius: 50%; border: 2px solid var(--white); }
  .slider-dots span.current { background: var(--white); }

  /* Welcome */
  .section-title { position: absolute; left: 0; width: 1200px; text-align: center; font-family: "Cinzel", Georgia, serif; font-size: 46px; font-weight: 400; color: var(--grey-title); letter-spacing: 1px; }
  .section-title .accent { color: var(--brand-blue); }
  .welcome-title { top: 745px; }
  .welcome-text { position: absolute; left: 136px; top: 816px; width: 928px; text-align: center; font-size: 16px; line-height: 25px; color: var(--text-grey); }

  /* Services */
  .services { position: absolute; top: 970px; left: 0; width: 1200px; height: 479px; background: var(--band-blue); }
  .services-photo { position: absolute; left: 0; top: 0; width: 370px; height: 479px; background: radial-gradient(ellipse at 60% 30%, #7fa9c6 0%, #2f6f97 45%, var(--band-blue) 100%); }
  .services-title { position: absolute; top: 52px; left: 0; width: 1200px; padding-left: 90px; text-align: center; font-family: "Cinzel", Georgia, serif; font-size: 44px; color: var(--white); letter-spacing: 1px; }
  .service { position: absolute; top: 145px; width: 340px; text-align: center; color: var(--white); }
  .service-recovery { left: 368px; }
  .service-debt { left: 785px; }
  .service-icon { width: 134px; height: 134px; margin: 0 auto; border-radius: 50%; background: var(--white); display: flex; align-items: center; justify-content: center; }
  .service-icon-inner { width: 110px; height: 110px; border-radius: 50%; background: var(--icon-fill); display: flex; align-items: center; justify-content: center; }
  .service-name { font-family: "Roboto Condensed", Arial, sans-serif; font-size: 27px; margin-top: 22px; }
  .service-text { font-size: 16px; line-height: 26px; margin-top: 12px; }

  /* News */
  .news-title { top: 1495px; }
  .news-item { position: absolute; top: 1567px; width: 235px; }
  .news-photo { width: 235px; height: 141px; }
  .news-headline { font-size: 17px; color: var(--brand-blue); margin-top: 12px; padding-left: 3px; }
  .news-date { font-size: 14px; color: var(--nav-grey); margin-top: 4px; display: flex; align-items: center; gap: 8px; padding-left: 3px; }
  .news-text { font-size: 16px; line-height: 25px; color: var(--text-grey); margin-top: 8px; padding-left: 2px; }

  /* Footer */
  .site-footer { position: absolute; top: 1893px; left: 0; width: 1200px; height: 329px; background: var(--footer-bg); }
  .contact-item { position: absolute; top: 26px; width: 300px; text-align: center; }
  .contact-icon { width: 82px; height: 82px; margin: 0 auto; border: 2px solid var(--footer-line); border-radius: 50%; display: flex; align-items: center; justify-content: center; }
  .contact-text { margin-top: 20px; font-size: 16px; color: var(--footer-text); }
  .footer-rule { position: absolute; top: 170px; left: 77px; width: 1046px; height: 1px; background: var(--footer-line); }
  .social-links { position: absolute; top: 202px; left: 501px; display: flex; gap: 20px; }
  .social-links span { width: 52px; height: 52px; background: #222222; }
  .social-links span.primary { background: var(--brand-blue); }
  .copyright { position: absolute; top: 270px; left: 0; width: 1200px; text-align: center; font-size: 14px; color: var(--white); }
</style>
</head>
<body>
<div class="page">

  <header class="site-header">
    <div class="brand">
      <div class="brand-mark"></div>
      <div>
        <div class="brand-name">BRISK HARBOR</div>
        <div class="brand-tagline">CLAIMS RECOVERY SERVICES</div>
      </div>
    </div>
    <nav class="main-nav">
      <a class="active">HOME</a>
      <a>ABOUT</a>
      <a>SERVICES</a>
      <a>CLIENTS</a>
      <a>BLOG</a>
      <a>CONTACT</a>
    </nav>
  </header>

  <section class="hero">
    <div class="hero-photo" role="img" aria-label="Overhead view of a business team meeting around a white table on a wooden floor"></div>
    <h1 class="hero-title">Managing your money,<br>recovering your<br>relationships</h1>
    <div class="hero-button">CONTACT US</div>
    <div class="slider-dots"><span class="current"></span><span></span><span></span><span></span><span></span></div>
  </section>

  <h2 class="section-title welcome-title">WELCOME TO <span class="accent">BRISK HARBOR</span></h2>
  <p class="welcome-text">We are a Claims Recovery and Debt Management Services company based in Dubai, United Arab Emirates. The Brisk Harbor team handles a comprehensive range of debt recoveries, such as invoices; insurance payments; supplier and rent payments; and personal and business loans, for individuals and businesses across an array of industries.</p>

  <section class="services">
    <div class="services-photo" role="img" aria-label="A hand touching a glowing round button"></div>
    <h2 class="services-title">SERVICES WE PROVIDE</h2>
    <div class="service service-recovery">
      <div class="service-icon"><div class="service-icon-inner">
        <svg width="66" height="56" viewBox="0 0 66 56" aria-hidden="true">
          <g fill="none" stroke="#fff">
            <circle cx="22" cy="30" r="12" stroke-width="8" stroke-dasharray="5 4"/>
            <circle cx="22" cy="30" r="8" stroke-width="5"/>
            <circle cx="48" cy="15" r="8" stroke-width="6" stroke-dasharray="4 3"/>
            <circle cx="48" cy="15" r="5" stroke-width="3"/>
            <circle cx="48" cy="42" r="8" stroke-width="6" stroke-dasharray="4 3"/>
            <circle cx="48" cy="42" r="5" stroke-width="3"/>
          </g>
        </svg>
      </div></div>
      <div class="service-name">Recovery Solutions</div>
      <p class="service-text">Our experience has taught us that when it comes to recovery, it always pays to find…</p>
    </div>
    <div class="service service-debt">
      <div class="service-icon"><div class="service-icon-inner">
        <svg width="62" height="56" viewBox="0 0 62 56" aria-hidden="true">
          <g fill="#fff">
            <rect x="22" y="2" width="18" height="14" rx="2"/>
            <rect x="2" y="38" width="16" height="14" rx="2"/>
            <rect x="23" y="38" width="16" height="14" rx="2"/>
            <rect x="44" y="38" width="16" height="14" rx="2"/>
          </g>
          <path d="M31 16v12M10 38v-10h42v10M31 28v10" stroke="#fff" stroke-width="3" fill="none"/>
        </svg>
      </div></div>
      <div class="service-name">Debt Management</div>
      <p class="service-text">At Brisk Harbor, we pull together our wisdom and expertise to make debt work for you.</p>
    </div>
  </section>

  <h2 class="section-title news-title">RECENT <span class="accent">NEWS</span></h2>

  <article class="news-item" style="left:77px">
    <div class="news-photo" role="img" aria-label="Two colleagues in a bright office meeting" style="background:linear-gradient(135deg,#e8eef2,#9aa9b6 55%,#c7cf9a)"></div>
    <h3 class="news-headline">Lorem Ipsum is dummy text.</h3>
    <div class="news-date"><svg width="12" height="12" viewBox="0 0 12 12" aria-hidden="true"><rect x="1" y="2" width="10" height="9" fill="none" stroke="#999" stroke-width="1.5"/><path d="M1 5h10" stroke="#999" stroke-width="1.5"/></svg>11 June 2016</div>
    <p class="news-text">Lorem Ipsum is simply dummy text of the printing and type setting industry.</p>
  </article>
  <article class="news-item" style="left:350px">
    <div class="news-photo" role="img" aria-label="Businessman and businesswoman signing papers at a desk" style="background:linear-gradient(135deg,#f1f1ee,#b8b2a6 50%,#6b5c4a)"></div>
    <h3 class="news-headline">Lorem Ipsum is dummy text.</h3>
    <div class="news-date"><svg width="12" height="12" viewBox="0 0 12 12" aria-hidden="true"><rect x="1" y="2" width="10" height="9" fill="none" stroke="#999" stroke-width="1.5"/><path d="M1 5h10" stroke="#999" stroke-width="1.5"/></svg>10 June 2016</div>
    <p class="news-text">Lorem Ipsum is simply dummy text of the printing and type setting industry.</p>
  </article>
  <article class="news-item" style="left:618px">
    <div class="news-photo" role="img" aria-label="Business handshake over a table" style="background:linear-gradient(135deg,#b7c3cf,#4a5868 55%,#2a3340)"></div>
    <h3 class="news-headline">Lorem Ipsum is dummy text.</h3>
    <div class="news-date"><svg width="12" height="12" viewBox="0 0 12 12" aria-hidden="true"><rect x="1" y="2" width="10" height="9" fill="none" stroke="#999" stroke-width="1.5"/><path d="M1 5h10" stroke="#999" stroke-width="1.5"/></svg>09 June 2016</div>
    <p class="news-text">Lorem Ipsum is simply dummy text of the printing and type setting industry.</p>
  </article>
  <article class="news-item" style="left:889px">
    <div class="news-photo" role="img" aria-label="Glass office tower seen from below" style="background:linear-gradient(135deg,#cfe0f3,#3f6fb0 50%,#16335e)"></div>
    <h3 class="news-headline">Lorem Ipsum is dummy text.</h3>
    <div class="news-date"><svg width="12" height="12" viewBox="0 0 12 12" aria-hidden="true"><rect x="1" y="2" width="10" height="9" fill="none" stroke="#999" stroke-width="1.5"/><path d="M1 5h10" stroke="#999" stroke-width="1.5"/></svg>08 June 2016</div>
    <p class="news-text">Lorem Ipsum is simply dummy text of the printing and type setting industry.</p>
  </article>

  <footer class="site-footer">
    <div class="contact-item" style="left:84px">
      <div class="contact-icon"><svg width="24" height="30" viewBox="0 0 24 30" aria-hidden="true"><path d="M12 1C6 1 2 5.5 2 11c0 7 10 18 10 18s10-11 10-18C22 5.5 18 1 12 1z" fill="#666"/><circle cx="12" cy="11" r="4" fill="#333"/></svg></div>
      <div class="contact-text">Lorem Ipsum is simply dummy text.</div>
    </div>
    <div class="contact-item" style="left:450px">
      <div class="contact-icon"><svg width="28" height="28" viewBox="0 0 28 28" aria-hidden="true"><path d="M6 2l5 6-3 3c1.5 3.5 5 7 9 9l3-3 6 5-3 4C13 25 3 15 2 5z" fill="#666"/></svg></div>
      <div class="contact-text">123 456 7890</div>
    </div>
    <div class="contact-item" style="left:816px">
      <div class="contact-icon"><svg width="30" height="22" viewBox="0 0 30 22" aria-hidden="true"><rect x="2" y="2" width="26" height="18" rx="2" fill="none" stroke="#666" stroke-width="2.5"/><path d="M3 4l12 9 12-9" fill="none" stroke="#666" stroke-width="2.5"/></svg></div>
      <div class="contact-text">info@briskharbor.com</div>
    </div>
    <div class="footer-rule"></div>
    <div class="social-links">
      <span class="primary" role="img" aria-label="Social network link"></span>
      <span role="img" aria-label="Social network link"></span>
      <span role="img" aria-label="Social network link"></span>
    </div>
    <p class="copyright">© <strong>BRISK HARBOR</strong> - 2016. All Right Reserved.</p>
  </footer>

</div>
</body>
</html>
```